Quillbrook IT company focused on 3 areas of IT

Looking for something similar to attached cards. Logo for quillbrook also attached.. Looking for something clean as far as colors (surprise me).. Quill stands for 3 primary areas, web design, consulting and network infrastructure design. Please email me if you have any questions. Looking forward to seeing how creative and professional this card will look. Thank you,

Target Market(s)

Small business/consumers looking for It services

Industry/Entity Type

It Service

Contact Information for Business Card

Dorin Vasek
Principal Consultant

202-555-0173

www.quillbrook-example.com
dvasek@quillbrook-example.com

27416 Copper Lantern Way,
Larkhaven, LK 20999

Colors

Designer to choose colors to be used in the design.

Requirements
Must have
• attached Logo design. Feel free to play with the colors.. If you have a better idea for a card, please fee free to send me. Looking for something clean/modern. Should have tech feel, not cheesy.
Nice to have
• Surprise me :-)..

```html
<!DOCTYPE html>
<html lang="en">
<head>
<meta charset="utf-8">
<title>Quillbrook — Business Card</title>
<link href="https://fonts.googleapis.com/css2?family=Saira+Condensed:wght@600&family=Work+Sans:wght@400;600&display=swap" rel="stylesheet">
<style>
  :root {
    --backdrop: #2a2a2c;
    --card: #1b1b1d;
    --accent: #27a7e1;
    --ink: #f4f4f4;
    --muted: #e2e2e2;
  }
  * { box-sizing: border-box; margin: 0; padding: 0; }
  html, body {
    width: 1200px;
    height: 900px;
    overflow: hidden;
    background: var(--backdrop);
    font-family: "Work Sans", Arial, sans-serif;
    color: var(--ink);
  }
  .sheet {
    width: 1200px;
    height: 900px;
    display: flex;
    flex-direction: column;
    align-items: center;
    justify-content: center;
    gap: 50px;
  }
  .card {
    position: relative;
    width: 630px;
    height: 360px;
    background: var(--card);
    border-bottom: 7px solid var(--accent);
    box-shadow: 0 14px 30px rgba(0,0,0,0.45);
  }

  /* Front */
  .card--front {
    display: flex;
    align-items: center;
    justify-content: center;
  }
  .brand {
    display: flex;
    align-items: center;
    gap: 16px;
  }
  .brand__mark {
    width: 22px;
    height: 22px;
    background: var(--accent);
  }
  .brand__name {
    font-family: "Work Sans", Arial, sans-serif;
    font-weight: 600;
    font-size: 44px;
    letter-spacing: 1px;
    color: var(--ink);
  }

  /* Back */
  .identity {
    position: absolute;
    left: 56px;
    top: 130px;
    width: 226px;
  }
  .identity__name {
    font-family: "Saira Condensed", "Arial Narrow", sans-serif;
    font-weight: 600;
    font-size: 42px;
    line-height: 1;
    letter-spacing: 2px;
    color: var(--accent);
    text-transform: uppercase;
    white-space: nowrap;
  }
  .identity__title {
    margin-top: 6px;
    font-size: 17px;
    letter-spacing: 0.6px;
    color: var(--muted);
    white-space: nowrap;
  }
  .divider {
    position: absolute;
    left: 294px;
    top: 128px;
    width: 2px;
    height: 66px;
    background: var(--accent);
  }
  .contact {
    position: absolute;
    left: 316px;
    top: 128px;
    list-style: none;
  }
  .contact__item {
    display: flex;
    align-items: center;
    gap: 10px;
    font-size: 15px;
    letter-spacing: 0.6px;
    line-height: 22px;
    color: var(--ink);
    white-space: nowrap;
  }
  .contact__icon {
    width: 11px;
    height: 11px;
    flex: none;
  }
  .address {
    position: absolute;
    left: 56px;
    bottom: 44px;
    font-size: 16px;
    letter-spacing: 0.8px;
    color: var(--ink);
    white-space: nowrap;
  }
</style>
</head>
<body>
<main class="sheet">
  <section class="card card--front" aria-label="Card front">
    <div class="brand">
      <span class="brand__mark"></span>
      <span class="brand__name">Quillbrook</span>
    </div>
  </section>

  <section class="card card--back" aria-label="Card back">
    <div class="identity">
      <h1 class="identity__name">Dorin Vasek</h1>
      <p class="identity__title">Principal Consultant</p>
    </div>
    <span class="divider"></span>
    <ul class="contact">
      <li class="contact__item">
        <svg class="contact__icon" viewBox="0 0 12 12" aria-hidden="true">
          <path d="M2.5 1 L4.5 1 L5.2 3.6 L4 4.6 Q5 7 7.4 8 L8.4 6.8 L11 7.5 L11 9.5 Q10.5 11 9 11 Q1 10 1 3 Q1 1.5 2.5 1 Z" fill="var(--accent)"/>
        </svg>
        202-555-0173
      </li>
      <li class="contact__item">
        <svg class="contact__icon" viewBox="0 0 12 12" aria-hidden="true">
          <rect x="0.8" y="2.3" width="10.4" height="7.4" fill="none" stroke="var(--accent)" stroke-width="1.2"/>
          <path d="M0.8 2.5 L6 6.6 L11.2 2.5" fill="none" stroke="var(--accent)" stroke-width="1.2"/>
        </svg>
        dvasek@quillbrook-example.com
      </li>
      <li class="contact__item">
        <svg class="contact__icon" viewBox="0 0 12 12" aria-hidden="true">
          <circle cx="6" cy="6" r="5" fill="none" stroke="var(--accent)" stroke-width="1.1"/>
          <ellipse cx="6" cy="6" rx="2.2" ry="5" fill="none" stroke="var(--accent)" stroke-width="1"/>
          <path d="M1 6 H11 M2 3.5 H10 M2 8.5 H10" stroke="var(--accent)" stroke-width="0.9"/>
        </svg>
        www.quillbrook-example.com
      </li>
    </ul>
    <p class="address">27416 Copper Lantern Way, Larkhaven, LK 20999</p>
  </section>
</main>
</body>
</html>
```